Modern card design needed for building development company

We are looking for a sharp modern new look for our business cards.
We are a New Zealand based company called TKR Ventures NZ LTD that specialises in subdividing large sections, housing and commercial buildings.
We have attached a photo of the current logo and would like to see it improved somehow as it looks a bit dated.
We are open to any colours.

Target Market(s)

Investors, Property buyers

Industry/Entity Type

Investment

Contact Information for Business Card

TKR VENTURES NZ LTD
www.tkrventuresnz.co.nz

Damon Whitcombe
Phone +64 21 938 104
Email dpwhitcombe@korumail.co.nz

Font styles to use
Serif
Sans Serif

Colors
0792cd
33a6d7
85cae6
6b449b
886aae
f04a50
ec1f27
f37122
f68d4d

Requirements
Must have
• Please try and make the logo more modern or if you have a similar one we would like to see it.

```html
<!DOCTYPE html>
<html lang="en">
<head>
<meta charset="utf-8">
<title>TKR Ventures NZ LTD – Business Card</title>
<link rel="stylesheet" href="https://fonts.googleapis.com/css2?family=Jost:wght@400;500&family=Oswald:wght@600&display=swap">
<style>
  :root {
    --backdrop: #2b2b2b;
    --card: #232323;
    --ink-white: #f2f2f2;
    --ink-grey: #8c8c8c;
    --accent: #33a6d7;
  }
  * { margin: 0; padding: 0; box-sizing: border-box; }
  html, body { width: 1200px; height: 904px; overflow: hidden; }
  body {
    background: var(--backdrop);
    font-family: "Jost", sans-serif;
    position: relative;
  }
  .card {
    position: absolute;
    left: 250px;
    width: 700px;
    height: 400px;
    background: var(--card);
    overflow: hidden;
  }
  .card--front { top: 32px; }
  .card--back { top: 472px; }

  /* front */
  .brand {
    position: absolute;
    top: 150px;
    left: 0; right: 0;
    display: flex;
    align-items: center;
    justify-content: center;
    gap: 14px;
  }
  .brand__mark { width: 18px; height: 18px; background: var(--ink-grey); }
  .brand__name {
    font-size: 34px;
    font-weight: 400;
    letter-spacing: 1px;
    color: var(--ink-grey);
  }
  .front-web {
    position: absolute;
    top: 290px;
    left: 0; right: 0;
    text-align: center;
    font-size: 17px;
    letter-spacing: 1.5px;
    color: var(--ink-white);
  }
  .accent { color: var(--accent); }

  /* back */
  .identity {
    position: absolute;
    top: 128px;
    right: 390px;
    text-align: right;
  }
  .identity__name {
    font-family: "Oswald", sans-serif;
    font-weight: 600;
    font-size: 36px;
    line-height: 1.05;
    color: var(--ink-white);
    text-transform: uppercase;
    white-space: nowrap;
  }
  .identity__role {
    font-size: 25px;
    font-weight: 500;
    color: var(--accent);
    letter-spacing: 0.5px;
  }
  .divider {
    position: absolute;
    top: 140px;
    left: 330px;
    width: 2px;
    height: 66px;
    background: var(--ink-white);
  }
  .contacts {
    position: absolute;
    top: 140px;
    left: 352px;
    list-style: none;
  }
  .contacts li {
    display: flex;
    align-items: center;
    gap: 12px;
    height: 23px;
    font-size: 17px;
    color: var(--ink-white);
    letter-spacing: 0.5px;
  }
  .contacts svg { width: 16px; height: 16px; flex: none; }
  .address {
    position: absolute;
    top: 318px;
    left: 150px;
    display: flex;
    align-items: center;
    gap: 14px;
    font-size: 19px;
    letter-spacing: 1px;
    color: var(--ink-white);
  }
  .address svg { width: 16px; height: 22px; }
  .stripe {
    position: absolute;
    left: 0; right: 0; bottom: 0;
    height: 12px;
    background: var(--accent);
  }
</style>
</head>
<body>
  <section class="card card--front">
    <div class="brand">
      <span class="brand__mark"></span>
      <span class="brand__name">TKR VENTURES NZ LTD</span>
    </div>
    <p class="front-web">www.<span class="accent">tkrventuresnz</span>.co.nz</p>
  </section>

  <section class="card card--back">
    <div class="identity">
      <h1 class="identity__name">Damon Whitcombe</h1>
      <p class="identity__role">Founder/CEO</p>
    </div>
    <div class="divider"></div>
    <ul class="contacts">
      <li>
        <svg viewBox="0 0 16 16" aria-hidden="true"><path d="M3 1l3 3-1.6 2a9 9 0 0 0 5.6 5.6L12 10l3 3-2 2C7 15 1 9 1 3z" fill="var(--accent)"/></svg>
        +64 21 938 104
      </li>
      <li>
        <svg viewBox="0 0 16 16" aria-hidden="true"><rect x="1" y="3" width="14" height="10" fill="none" stroke="var(--accent)" stroke-width="1.5"/><path d="M1 3l7 6 7-6" fill="none" stroke="var(--accent)" stroke-width="1.5"/></svg>
        dpwhitcombe@korumail.co.nz
      </li>
      <li>
        <svg viewBox="0 0 16 16" aria-hidden="true"><g fill="none" stroke="var(--accent)" stroke-width="1.3"><circle cx="8" cy="8" r="6.5"/><ellipse cx="8" cy="8" rx="3" ry="6.5"/><path d="M1.5 8h13M2.5 4.5h11M2.5 11.5h11"/></g></svg>
        <span>www.<span class="accent">tkrventuresnz</span>.co.nz</span>
      </li>
    </ul>
    <p class="address">
      <svg viewBox="0 0 16 22" aria-hidden="true"><path d="M8 0a8 8 0 0 0-8 8c0 6 8 14 8 14s8-8 8-14a8 8 0 0 0-8-8z" fill="var(--accent)"/><circle cx="8" cy="8" r="3" fill="var(--card)"/></svg>
      Your Street Address, New Zealand, 1234
    </p>
    <div class="stripe"></div>
  </section>
</body>
</html>
```